Sunset Harbor Living Web Page

We need a web page design that has two intro pages - first being a 'home page', then a link to the second page that has the 'content tabs' and a 'call to action' (see below).

The business helps people that wish to retire to S.E.Asia (Thailand, Malaysia, Indonesia,The Philippines etc) - to enjoy the lifestyle and the remaining years of their lives. What attracts S.E.Asia to many people is the lower cost, the atmoshpere and beauty of the tropics and the vibrancy of the various countries.

People that are wishing to make the most of their retirement and are adventurous at a great bargain compared to the cost of their own countries will be interested.

We help them achieve this - visa, financials (tax, gov't payments etc), introduce them to the right people for property, clubs, retirement facilities, insurance and so forth.

Therefore we are providing an extremely wide ranging service and this site will provide broad but general information only - with a call to action to come and see us for more specific information and how we can help them specifically.

This site will be predominantly for travel and lifestyle, it will be linked with another financial services (financial planning) site later down the track.

The colour scheme is dark green and blue - as per the attached logo design. Photos and background just think lifestyle and S.E.Asia - beaches/mountains/water/recreational activities for retirees.

Target market is mostly those coming up to retirement to those that are already retired. But we also expect to have some interest with younger people that would like to find out more and plan for the future. So a broad age group but I would say mostly 40-70 yrs old.

On the first (Home) page we would like our company name 'Sunset Harbor Living', our logo (which will be on all pages) and a statement such as: “Imagine a retirement where your dreams are brought to life, and you have never felt more alive. Let us show you how”. Then a link to the second page.

We would like an uncluttered site. On the second (contents) page the tabs would be:

- Visa
- Property
- Financials
- Travel
- Insurance & Healthcare
- Medical Tourism
- Cost of living
- Weekly Blogs and articles
- Sunset Harbor Living story

We would also like a call to action on the second page - asking them to leave their contact details if they wish to learn more or sign up to our weekly newsletter/blog.

We are open to suggestions and your imaginations.

Thank you
Malcolm

Font styles to use
Serif
Script

Colors
0255a3
3377b5
00a990
9bcb3c
abd036
33b8a4
85abd2
cadf82
86cfc6

Requirements
Must have
• I have been asked by the web designer to receive a 'Web Font' so that we can 'get off of Zentrofy'. Hope that makes sense.

```html
<!DOCTYPE html>
<html lang="en">
<head>
<meta charset="utf-8">
<title>Sunset Harbor Living</title>
<link rel="stylesheet" href="https://fonts.googleapis.com/css2?family=Cinzel:wght@400;600&family=Great+Vibes&family=Open+Sans:wght@400;600;700&family=Roboto+Condensed:wght@400;700&display=swap">
<style>
:root{
  --green:#1f9e57;
  --green-dark:#178748;
  --blue:#1190d6;
  --blue-dark:#0d75b8;
  --footer-blue:#1585cf;
  --ink:#333;
  --muted:#666;
  --card-grey:#e6e6e6;
  --band-grey:#ececec;
  --nav-black:#111;
  --white:#fff;
}
*{box-sizing:border-box;margin:0;padding:0}
html,body{width:1200px;height:3689px;overflow:hidden}
body{position:relative;font-family:"Open Sans",Arial,sans-serif;color:var(--ink);background:var(--white)}
.abs{position:absolute}

/* top nav */
.topnav{top:0;left:0;width:1200px;height:34px;background:var(--nav-black);display:flex;align-items:center;padding-left:60px;z-index:3}
.topnav a{color:var(--white);font-size:13px;text-decoration:none;padding:0 13px;border-right:1px solid #555;font-family:"Roboto Condensed",sans-serif;letter-spacing:.3px}
.topnav a:last-child{border-right:0}

/* hero */
.hero{top:0;left:0;width:1200px;height:681px;overflow:hidden}
.hero-photo{position:absolute;inset:0;background:
  radial-gradient(ellipse 380px 520px at 930px 230px,rgba(92,78,58,.85),rgba(92,78,58,0) 70%),
  radial-gradient(ellipse 260px 120px at 200px 560px,rgba(110,74,44,.7),rgba(110,74,44,0) 70%),
  linear-gradient(180deg,#8c9aa3 0%,#a9b3b5 22%,#7d8f83 40%,#4f8a86 58%,#3fa5a0 74%,#7cc3b6 90%,#c6d9c1 100%)}
.hero-shade{position:absolute;inset:0;background:rgba(0,0,0,.18)}
.contact-item{display:flex;align-items:center;gap:10px;color:var(--white);font-size:14px;line-height:17px}
.contact-item b{font-weight:700}
.icon-circle{width:32px;height:32px;border-radius:50%;background:var(--green);display:flex;align-items:center;justify-content:center}
.brand{top:62px;left:0;width:1200px;text-align:center;color:var(--white)}
.brand-mark{width:58px;height:58px;border-radius:50%;background:var(--green);margin:0 auto 6px}
.brand-name{font-weight:700;font-size:26px}
.utility{top:50px;left:912px;display:flex;gap:16px}
.utility a{color:var(--white);font-size:12px;text-decoration:none;font-weight:600}
.socials{display:flex;gap:8px}
.socials span{width:36px;height:36px;background:rgba(255,255,255,.8);display:block}
.hero-arrow{width:30px;height:30px;border-radius:50%;background:rgba(0,0,0,.6);border:2px solid #fff;top:430px}
.hero-copy{top:315px;left:0;width:1200px;text-align:center;color:var(--white);font-family:"Cinzel",serif}
.hero-copy .imagine{font-size:66px;letter-spacing:28px;line-height:80px;padding-left:28px}
.hero-copy .a-line{display:flex;align-items:center;justify-content:center;gap:20px;height:54px}
.hero-copy .rule{width:260px;height:2px;background:#fff}
.script{font-family:"Great Vibes",cursive;text-transform:none;letter-spacing:0}
.hero-copy .a-line .script{font-size:52px}
.hero-copy .big{font-size:48px;line-height:60px}
.hero-copy .big .script{font-size:56px}
.hero-copy .small{font-size:27px;line-height:36px;border-bottom:2px solid #fff;display:inline-block;padding:0 6px 14px}

/* welcome */
.welcome{top:681px;left:0;width:1200px;height:327px;background:var(--green);color:var(--white);text-align:center}
.welcome h2{font-size:22px;font-weight:700;margin-top:52px}
.welcome .dot{width:22px;height:14px;border-radius:14px 14px 0 0;background:#fff;margin:8px auto 0}
.welcome p{width:1020px;margin:12px auto 0;font-size:14px;line-height:24px}
.btn-outline{display:inline-block;border:2px solid #fff;color:#fff;font-size:12px;padding:5px 12px;margin-top:30px;border-radius:3px;font-weight:600}

/* feature cards */
.card{top:1062px;width:316px;height:394px;background:var(--card-grey);border-top:4px solid var(--green);padding:14px 16px}
.card-head{display:flex;justify-content:space-between;align-items:flex-start;height:52px}
.card-head h3{color:var(--blue);font-family:"Roboto Condensed",sans-serif;font-size:17px;line-height:19px;font-weight:400;text-transform:uppercase}
.mini-mark{width:34px;height:34px;border-radius:50%;background:var(--green)}
.card-photo{height:152px;margin-top:6px}
.card p{font-size:13.5px;line-height:21px;color:var(--muted);margin-top:12px}
.btn-green{display:inline-flex;align-items:center;gap:6px;background:var(--green);color:#fff;font-size:12px;font-weight:600;padding:5px 10px;border-radius:2px}
.btn-green i{width:11px;height:11px;border:1.5px solid #fff;border-radius:50%;display:block}
.card .btn-green{margin-top:22px}

/* list property */
.listing{top:1505px;left:0;width:1200px;height:393px;background:var(--band-grey);text-align:center}
.listing .mini-mark{margin:24px auto 0}
.listing h2{color:var(--blue);font-family:"Roboto Condensed",sans-serif;font-size:24px;font-weight:400;margin-top:6px}
.property{top:101px;width:216px}
.property .photo{height:160px}
.property span{display:block;text-align:left;font-size:13px;color:var(--muted);margin-top:8px}
.nav-circle{width:32px;height:32px;border-radius:50%;background:var(--blue);display:flex;align-items:center;justify-content:center}

/* lifestyle */
.lifestyle-title{top:1948px;left:0;width:1200px;text-align:center;font-family:"Roboto Condensed",sans-serif}
.lifestyle-title .l1{display:flex;align-items:center;justify-content:center;gap:16px;color:var(--blue);font-size:40px;line-height:44px}
.lifestyle-title .l1 .mini-mark{width:40px;height:28px;border-radius:20px 20px 0 0}
.lifestyle-title .l2{color:var(--green);font-size:23px;line-height:26px}
.country{top:2048px;width:334px}
.country-bar{height:45px;background:var(--blue);color:#fff;font-family:"Roboto Condensed",sans-serif;font-size:17px;line-height:45px;padding-left:18px}
.country-photo{height:187px}
.country h4{font-family:"Roboto Condensed",sans-serif;font-size:15px;font-weight:700;margin-top:16px;line-height:20px}
.country .lead{font-size:12.5px;color:var(--muted);line-height:19px;margin-top:4px;height:52px;border-bottom:1px solid #ddd}
.story{display:flex;gap:12px;margin-top:10px;height:80px;border-bottom:1px solid #e3e3e3}
.story:last-child{border-bottom:0}
.story .thumb{width:70px;height:70px;flex:none}
.story b{display:block;font-size:13px;color:#222}
.story small{display:block;font-size:12px;color:var(--muted);line-height:17px;margin-top:3px}
.view-bar{top:2660px;left:74px;width:1052px;height:14px;background:#ddd}
.view-more{top:2654px;left:545px}

/* bottom panels */
.panel{top:2747px;width:334px;height:396px;box-shadow:0 2px 4px rgba(0,0,0,.2)}
.panel-blue{background:var(--blue);color:#fff}
.panel-green{background:var(--green);color:#fff}
.panel h3{font-family:"Roboto Condensed",sans-serif;font-size:17px;font-weight:400;padding:18px 16px 0}
.video{margin:16px 16px 0;height:212px;position:relative}
.play{position:absolute;left:118px;top:72px;width:56px;height:56px;border-radius:50%;background:var(--green);display:flex;align-items:center;justify-content:center}
.panel-blue p{font-size:13.5px;line-height:21px;padding:10px 16px}
.quote{margin:16px 16px 0;background:#fff;color:#444;height:271px;padding:20px 22px;border-radius:3px}
.quote p{font-style:italic;font-size:13px;line-height:21px}
.quote .who{display:flex;align-items:center;gap:12px;margin-top:14px;font-weight:700;font-size:13px}
.avatar{width:54px;height:54px;border-radius:50%;background:#d8cfc6}
.quote-nav{display:flex;justify-content:center;gap:12px;margin-top:14px}
.quote-nav span{width:30px;height:30px;border-radius:50%;border:2px solid #fff;display:flex;align-items:center;justify-content:center}
.panel-tabs{background:#fff;border:1px solid #ddd}
.tabs{display:flex;height:52px;border-bottom:1px solid #ddd}
.tabs span{flex:1;text-align:center;line-height:52px;font-family:"Roboto Condensed",sans-serif;font-size:17px;color:#333}
.tabs span.on{color:var(--blue);border-right:1px solid #ddd}
.blog{display:flex;gap:12px;padding:18px 18px 0}
.blog .thumb{width:64px;height:64px;flex:none}
.blog b{font-size:13px;display:block}
.blog small{font-size:12px;color:var(--muted);line-height:17px;display:block;margin-top:3px}
.panel-tabs .btn-green{margin:22px 18px 0}

/* footer */
.footer{top:3150px;left:0;width:1200px;height:539px}
.footer-mark{top:56px;left:550px;width:100px;height:100px;border-radius:50%;background:var(--green)}
.footer-body{position:absolute;top:96px;left:0;width:1200px;height:418px;background:var(--footer-blue);color:#fff}
.footer h5{font-size:12px;font-weight:700;letter-spacing:.5px}
.footer .links{font-size:12.5px;line-height:24px}
.footer .sub-text{font-size:12.5px;line-height:20px;width:290px}
.footer .field{width:272px;height:32px;background:#fff;color:#888;font-size:12px;line-height:32px;padding-left:10px;margin-top:10px}
.footer .sub-btn{display:inline-block;background:#3aa6e6;font-size:12px;font-weight:700;padding:7px 12px;margin-top:12px}
.socials.foot span{width:36px;height:36px;background:rgba(255,255,255,.9)}
.contact-row{display:flex;gap:40px;align-items:center;font-size:17px}
.contact-row div{display:flex;align-items:center;gap:10px}
.ring{width:32px;height:32px;border-radius:50%;border:2px solid #fff;display:flex;align-items:center;justify-content:center}
.foot-brand{display:flex;align-items:center;gap:10px;font-weight:700;font-size:26px}
.foot-brand i{width:44px;height:44px;border-radius:50%;background:#fff;display:block}
.copyright{position:absolute;top:514px;left:0;width:1200px;height:25px;background:var(--green);color:#fff;font-size:12px;text-align:center;line-height:25px}
</style>
</head>
<body>

<nav class="abs topnav">
  <a>VISA</a><a>PROPERTY</a><a>FINANCIALS</a><a>TRAVEL</a><a>INSURANCE &amp; HEALTHCARE</a><a>MEDICAL TOURISM</a><a>COST OF LIVING</a><a>WEEKLY BLOGS &amp; ARTICLES</a><a>SUNSET HARBOR LIVING STORY</a>
</nav>

<header class="abs hero">
  <div class="hero-photo" role="img" aria-label="Tropical bay with limestone cliffs and a long-tail boat on turquoise water"></div>
  <div class="hero-shade"></div>

  <div class="abs contact-item" style="top:76px;left:74px">
    <span class="icon-circle"><svg width="16" height="16" viewBox="0 0 24 24"><path fill="#fff" d="M6.6 10.8a15 15 0 006.6 6.6l2.2-2.2a1 1 0 011-.25 11.4 11.4 0 003.6.57 1 1 0 011 1V20a1 1 0 01-1 1A17 17 0 013 4a1 1 0 011-1h3.5a1 1 0 011 1c0 1.25.2 2.45.57 3.6a1 1 0 01-.25 1z"/></svg></span>
    <span>Call Us:<br><b>+1-000-000-0000</b></span>
  </div>
  <div class="abs contact-item" style="top:76px;left:270px">
    <span class="icon-circle"><svg width="16" height="16" viewBox="0 0 24 24"><path fill="#fff" d="M3 5h18v14H3z"/><path d="M3 6l9 7 9-7" stroke="#1f9e57" stroke-width="2" fill="none"/></svg></span>
    <span>Email Us:<br><b>info@sunsetharborliving.com</b></span>
  </div>

  <div class="abs brand">
    <div class="brand-mark"></div>
    <div class="brand-name">Sunset Harbor Living</div>
  </div>

  <div class="abs utility"><a>HOME</a><a>ABOUT US</a><a>CONTACT US</a></div>
  <div class="abs socials" style="top:78px;left:908px"><span></span><span></span><span></span><span></span><span></span></div>

  <div class="abs hero-arrow" style="left:42px"><svg width="26" height="26" viewBox="0 0 26 26"><path d="M15 8l-5 5 5 5" stroke="#fff" stroke-width="2.5" fill="none"/></svg></div>
  <div class="abs hero-arrow" style="left:1124px"><svg width="26" height="26" viewBox="0 0 26 26"><path d="M11 8l5 5-5 5" stroke="#fff" stroke-width="2.5" fill="none"/></svg></div>

  <div class="abs hero-copy">
    <div class="imagine">IMAGINE</div>
    <div class="a-line"><span class="rule"></span><span class="script">a</span><span class="rule"></span></div>
    <div class="big">RETIREMENT WHERE <span class="script">your</span> DREAMS</div>
    <div class="small">ARE BROUGHT TO LIFE.AND YOU HAVE NEVER FELT MORE ALIVE.</div>
  </div>
</header>

<section class="abs welcome">
  <h2>WELCOME TO SUNSET HARBOR LIVING</h2>
  <div class="dot"></div>
  <p>Lorem ipsum dolor sit amet, consectetur adipiscing elit, sed do eiusmod tempor incididunt ut labore et dolore magna aliqua. Ut enim ad minim veniam, quis nostrud exercitation ullamco laboris nisi ut aliquip ex ea commodo consequat. Duis aute irure dolor in reprehenderit in voluptate velit esse cillum dolore eu fugiat nulla pariatur. Excepteur sint occaecat cupidatat non proident, sunt in culpa qui officia deserunt mollit anim id est laborum.</p>
  <span class="btn-outline">READ MORE ⊙</span>
</section>

<article class="abs card" style="left:74px">
  <div class="card-head"><h3>What about your<br>financial future?</h3><span class="mini-mark"></span></div>
  <div class="card-photo" role="img" aria-label="Hands using a tablet with financial charts" style="background:linear-gradient(160deg,#1e3f66 0%,#3f6f9f 45%,#a9c4de 100%)"></div>
  <p>Lorem ipsum dolor sit amet, consectetur adipiscing elit, sed do eiusmod tempor incididunt ut labore et dolore magna aliqua. Ut enim ad</p>
  <span class="btn-green">READ MORE <i></i></span>
</article>
<article class="abs card" style="left:433px">
  <div class="card-head"><h3>Insurance &amp;<br>Healthcare</h3><span class="mini-mark"></span></div>
  <div class="card-photo" role="img" aria-label="Medical insurance policy form with a stethoscope" style="background:linear-gradient(160deg,#eef2f6 0%,#c4d6e8 50%,#6f95bb 100%)"></div>
  <p>Lorem ipsum dolor sit amet, consectetur adipiscing elit, sed do eiusmod tempor incididunt ut labore et dolore magna aliqua. Ut enim ad</p>
  <span class="btn-green">READ MORE <i></i></span>
</article>
<article class="abs card" style="left:792px;width:334px">
  <div class="card-head"><h3>Medical<br>Tourism</h3><span class="mini-mark"></span></div>
  <div class="card-photo" role="img" aria-label="World map with a stethoscope laid over it" style="background:linear-gradient(160deg,#e6d7ae 0%,#cbd0b4 50%,#8fbfd1 100%)"></div>
  <p>Lorem ipsum dolor sit amet, consectetur adipiscing elit, sed do eiusmod tempor incididunt ut labore et dolore magna aliqua. Ut enim ad</p>
  <span class="btn-green">READ MORE <i></i></span>
</article>

<section class="abs listing">
  <div class="mini-mark"></div>
  <h2>LIST A PROPERTY!</h2>
  <div class="abs nav-circle" style="left:75px;top:176px"><svg width="14" height="14" viewBox="0 0 14 14"><path d="M9 2L4 7l5 5" stroke="#fff" stroke-width="2.2" fill="none"/></svg></div>
  <div class="abs property" style="left:133px"><div class="photo" role="img" aria-label="Traditional Thai house with carved roof" style="background:linear-gradient(180deg,#8fc0e6 0%,#b9d6ec 30%,#b5652c 50%,#8a4a22 70%,#6e8f45 100%)"></div><span>Lorem House for Sale</span></div>
  <div class="abs property" style="left:371px"><div class="photo" role="img" aria-label="Wooden temple-style house among trees" style="background:linear-gradient(180deg,#a6cdee 0%,#d4e6f3 30%,#6a4a2e 52%,#4b3320 72%,#5f7f3c 100%)"></div><span>Lorem House for Sale</span></div>
  <div class="abs property" style="left:610px"><div class="photo" role="img" aria-label="Thai style villa with garden" style="background:linear-gradient(180deg,#dbe9f4 0%,#eef4f8 30%,#9a5a2a 52%,#7a4420 72%,#4f7a35 100%)"></div><span>Lorem House for Sale</span></div>
  <div class="abs property" style="left:848px"><div class="photo" role="img" aria-label="Traditional Thai house with carved roof" style="background:linear-gradient(180deg,#8fc0e6 0%,#b9d6ec 30%,#b5652c 50%,#8a4a22 70%,#6e8f45 100%)"></div><span>Lorem House for Sale</span></div>
  <div class="abs nav-circle" style="left:1091px;top:176px"><svg width="14" height="14" viewBox="0 0 14 14"><path d="M5 2l5 5-5 5" stroke="#fff" stroke-width="2.2" fill="none"/></svg></div>
  <span class="abs btn-green" style="left:526px;top:322px">LIST A PROPERTY! <i></i></span>
</section>

<div class="abs lifestyle-title">
  <div class="l1"><span class="mini-mark"></span>ENJOY THE LIFESTYLE AND<span class="mini-mark"></span></div>
  <div class="l2">THE REMAINING YEARS OF THEIR LIVES</div>
</div>

<section class="abs country" style="left:74px">
  <div class="country-bar">RETIRE TO THAILAND</div>
  <div class="country-photo" role="img" aria-label="Limestone island rising from a turquoise bay" style="background:linear-gradient(180deg,#c6dff0 0%,#e4eef4 25%,#6f8a64 45%,#4d6b4f 60%,#3fb3b0 78%,#9fd9d2 100%)"></div>
  <h4>LIFESTYLE IN THAILAND</h4>
  <div class="lead">Lorem ipsum dolor sit amet, consectetur adipiscing elit</div>
  <div class="story"><div class="thumb" role="img" aria-label="Jungle walking path" style="background:linear-gradient(180deg,#9bb67a,#5d7c40)"></div><div><b>Lorem ipsum dolor sit amet</b><small>Sed ut perspiciatis unde omnis iste natus error sit voluptatem.</small></div></div>
  <div class="story"><div class="thumb" role="img" aria-label="Sunset over the sea" style="background:linear-gradient(180deg,#e8b47a,#b97f4c 60%,#6d8fa0)"></div><div><b>Lorem ipsum dolor sit amet</b><small>Sed ut perspiciatis unde omnis iste natus error sit voluptatem.</small></div></div>
  <div class="story"><div class="thumb" role="img" aria-label="Rock island in the bay" style="background:linear-gradient(180deg,#b9d4e4,#5e7f60 50%,#4fb0aa)"></div><div><b>Lorem ipsum dolor sit amet</b><small>Sed ut perspiciatis unde omnis iste natus error sit voluptatem.</small></div></div>
</section>
<section class="abs country" style="left:433px">
  <div class="country-bar">RETIRE TO MALAYSIA</div>
  <div class="country-photo" role="img" aria-label="Illuminated red and gold temple at night" style="background:linear-gradient(180deg,#1d3d7a 0%,#3d4f8a 25%,#b8402c 55%,#d8772f 75%,#e0a43a 100%)"></div>
  <h4>LIFESTYLE IN MALAYSIA</h4>
  <div class="lead">Lorem ipsum dolor sit amet, consectetur adipiscing elit</div>
  <div class="story"><div class="thumb" role="img" aria-label="Beach with boats" style="background:linear-gradient(180deg,#bfe0f0,#5fb6c9 55%,#e6dcc0)"></div><div><b>Lorem ipsum dolor sit amet</b><small>Sed ut perspiciatis unde omnis iste natus error sit voluptatem.</small></div></div>
  <div class="story"><div class="thumb" role="img" aria-label="Beach with boats" style="background:linear-gradient(180deg,#bfe0f0,#5fb6c9 55%,#e6dcc0)"></div><div><b>Lorem ipsum dolor sit amet</b><small>Sed ut perspiciatis unde omnis iste natus error sit voluptatem.</small></div></div>
  <div class="story"><div class="thumb" role="img" aria-label="Beach with boats" style="background:linear-gradient(180deg,#bfe0f0,#5fb6c9 55%,#e6dcc0)"></div><div><b>Lorem ipsum dolor sit amet</b><small>Sed ut perspiciatis unde omnis iste natus error sit voluptatem.</small></div></div>
</section>
<section class="abs country" style="left:792px">
  <div class="country-bar">RETIRE TO THE PHILIPPINES</div>
  <div class="country-photo" role="img" aria-label="Green islands in a tropical lagoon" style="background:linear-gradient(180deg,#b7d6ec 0%,#d9e8f2 22%,#5f8c4f 42%,#3f6f3c 60%,#3a9a94 80%,#7cc6be 100%)"></div>
  <h4>LIFESTYLE IN THE PHILIPPINES</h4>
  <div class="lead">Lorem ipsum dolor sit amet, consectetur adipiscing elit</div>
  <div class="story"><div class="thumb" role="img" aria-label="Beach with boats" style="background:linear-gradient(180deg,#bfe0f0,#5fb6c9 55%,#e6dcc0)"></div><div><b>Lorem ipsum dolor sit amet</b><small>Sed ut perspiciatis unde omnis iste natus error sit voluptatem.</small></div></div>
  <div class="story"><div class="thumb" role="img" aria-label="Beach with boats" style="background:linear-gradient(180deg,#bfe0f0,#5fb6c9 55%,#e6dcc0)"></div><div><b>Lorem ipsum dolor sit amet</b><small>Sed ut perspiciatis unde omnis iste natus error sit voluptatem.</small></div></div>
  <div class="story"><div class="thumb" role="img" aria-label="Beach with boats" style="background:linear-gradient(180deg,#bfe0f0,#5fb6c9 55%,#e6dcc0)"></div><div><b>Lorem ipsum dolor sit amet</b><small>Sed ut perspiciatis unde omnis iste natus error sit voluptatem.</small></div></div>
</section>
<div class="abs view-bar"></div>
<span class="abs btn-green view-more">VIEW MORE <i></i></span>

<section class="abs panel panel-blue" style="left:74px">
  <h3>LISTEN TO WHAT THIS SITE IS ABOUT</h3>
  <div class="video" role="img" aria-label="Video still of a presenter" style="background:linear-gradient(135deg,#f0ece7 0%,#cfc3b6 45%,#4a3f38 100%)">
    <span class="play"><svg width="22" height="22" viewBox="0 0 22 22"><path d="M7 4l11 7-11 7z" fill="#fff"/></svg></span>
  </div>
  <p>Lorem ipsum dolor sit amet, consectetur adipiscing elit, sed do eiusmod tempor incididunt ut labore et dolore magna aliqua. Ut enim ad</p>
</section>
<section class="abs panel panel-green" style="left:433px">
  <h3>SUNSET HARBOR LIVING STORY</h3>
  <div class="quote">
    <p>“Lorem ipsum dolor sit amet, consectetur adipiscing elit, sed do eiusmod tempor incididunt ut labore et dolore magna aliqua. Ut enim ad minim veniam, quis nostrud exercitation ullamco laboris nisi ut aliquip ex ea commodo”</p>
    <div class="who"><span class="avatar" role="img" aria-label="Customer portrait"></span>-John Doe</div>
  </div>
  <div class="quote-nav">
    <span><svg width="12" height="12" viewBox="0 0 12 12"><path d="M8 2L4 6l4 4" stroke="#fff" stroke-width="2" fill="none"/></svg></span>
    <span><svg width="12" height="12" viewBox="0 0 12 12"><path d="M4 2l4 4-4 4" stroke="#fff" stroke-width="2" fill="none"/></svg></span>
  </div>
</section>
<section class="abs panel panel-tabs" style="left:792px">
  <div class="tabs"><span class="on">WEEKLY BLOGS</span><span>ARTICLES</span></div>
  <div class="blog"><div class="thumb" role="img" aria-label="Retired couple outdoors" style="background:linear-gradient(180deg,#d6e2c6,#9cb581)"></div><div><b>Lorem ipsum dolor sit amet</b><small>July 2, 2015. No Comments on Ut enim ad minim veniam.</small></div></div>
  <div class="blog"><div class="thumb" role="img" aria-label="Retired couple smiling" style="background:linear-gradient(180deg,#ead9c4,#c29f7c)"></div><div><b>Lorem ipsum dolor sit amet</b><small>July 2, 2015. No Comments on Ut enim ad minim veniam.</small></div></div>
  <div class="blog"><div class="thumb" role="img" aria-label="Retirees relaxing together" style="background:linear-gradient(180deg,#d2dbe6,#94a8be)"></div><div><b>Lorem ipsum dolor sit amet</b><small>July 2, 2015. No Comments on Ut enim ad minim veniam.</small></div></div>
  <span class="btn-green">READ MORE <i></i></span>
</section>

<footer class="abs footer">
  <svg class="abs" style="top:60px;left:0" width="1200" height="40" viewBox="0 0 1200 40" preserveAspectRatio="none">
    <path d="M0 22 C80 6 140 30 220 14 S360 2 440 20 S560 34 620 14 S760 4 840 22 S980 30 1060 12 S1160 8 1200 18 L1200 40 L0 40Z" fill="#1585cf"/>
  </svg>
  <div class="abs footer-mark"></div>
  <div class="footer-body">
    <h5 class="abs" style="top:122px;left:74px">QUICK LINKS</h5>
    <div class="abs links" style="top:144px;left:74px">Visa<br>Property<br>Financials<br>Travel<br>Insurance &amp; Healthcare</div>
    <div class="abs links" style="top:144px;left:229px">Medical Tourism<br>Cost of living<br>Weekly Blogs &amp; articles<br>Sunset Harbor Living story</div>
    <h5 class="abs" style="top:122px;left:406px">MORE LINKS</h5>
    <div class="abs links" style="top:144px;left:406px">Careers<br>Privacy Policy<br>Terms And Conditions<br>Traveler Resources</div>
    <h5 class="abs" style="top:122px;left:573px">SUBSCRIBE TO OUR NEWSLETTER</h5>
    <div class="abs" style="top:148px;left:573px">
      <div class="sub-text">Keep up to date with our new hire products and special offers</div>
      <div class="field">Enter your email address</div>
      <span class="sub-btn">SUBSCRIBE</span>
    </div>
    <h5 class="abs" style="top:122px;left:883px">FOLLOW US</h5>
    <div class="abs socials foot" style="top:154px;left:883px"><span></span><span></span><span></span><span></span><span></span></div>
    <h5 class="abs" style="top:332px;left:74px">CONTACT US</h5>
    <div class="abs contact-row" style="top:360px;left:74px">
      <div><span class="ring"><svg width="14" height="14" viewBox="0 0 24 24"><path fill="#fff" d="M6.6 10.8a15 15 0 006.6 6.6l2.2-2.2a1 1 0 011-.25 11.4 11.4 0 003.6.57 1 1 0 011 1V20a1 1 0 01-1 1A17 17 0 013 4a1 1 0 011-1h3.5a1 1 0 011 1c0 1.25.2 2.45.57 3.6a1 1 0 01-.25 1z"/></svg></span>+1-000-000-0000</div>
      <div><span class="ring"><svg width="14" height="14" viewBox="0 0 24 24"><path fill="#fff" d="M3 5h18v14H3z"/><path d="M3 6l9 7 9-7" stroke="#1585cf" stroke-width="2" fill="none"/></svg></span>info@sunsetharborliving.com</div>
    </div>
    <div class="abs foot-brand" style="top:340px;left:832px"><i></i>Sunset Harbor Living</div>
  </div>
  <div class="copyright">© 2016 Sunset Harbor Living. All Rights Reserved</div>
</footer>

</body>
</html>
```